Hoist Ridge Crane Sales Flyer

I need a professional modern flyer offering our crane services with our phone number and website. The flyer should focus on the blue crane and the red crane (KnuckleBooms) but include a small picture of the other cranes as well to show variety. This flyer will be mailed and emailed to a variety of roofing companies, HVAC, pool and mechanical contractors as well as precast concrete companies to attempt to earn their business. 8.5x11 single sided

HoistRidgeCranes.example
555 417-2093 should be number on flyer

```html
<!DOCTYPE html>
<html lang="en">
<head>
<meta charset="utf-8">
<title>Hoist Ridge Crane – Crane Service Flyer</title>
<link href="https://fonts.googleapis.com/css2?family=Oswald:wght@700&family=Poppins:ital,wght@0,400;0,500;0,600;0,700;1,700;1,800&display=swap" rel="stylesheet">
<style>
  :root{
    --red:#c01b2c;
    --ink:#121212;
    --dark:#1b1b1c;
    --white:#ffffff;
    --green:#2f9a45;
  }
  *{box-sizing:border-box;margin:0;padding:0}
  html,body{width:783px;height:1200px;overflow:hidden;background:#fff}
  body{font-family:"Poppins",sans-serif;color:var(--white)}
  .flyer{position:relative;width:783px;height:1200px;overflow:hidden;background:var(--dark)}
  .abs{position:absolute}

  /* hero */
  .hero{left:0;top:0;width:783px;height:493px;background:#fff}
  .hero-photo{left:0;top:0;width:783px;height:493px;
    background:linear-gradient(90deg,#ffffff 0%,#f4f6f8 30%,rgba(244,246,248,0) 48%),
               linear-gradient(180deg,#a9c5e4 0%,#d5e0ea 40%,#8d9299 62%,#a6a8aa 100%)}
  .brand{left:52px;top:90px;display:flex;align-items:center;gap:8px}
  .brand-dot{width:14px;height:14px;border-radius:50%;background:var(--red)}
  .brand-name{font-weight:700;font-size:17px;color:var(--ink);letter-spacing:.3px}
  .headline{left:42px;top:148px;font-family:"Oswald",sans-serif;font-style:italic;font-weight:700;line-height:.92;text-transform:uppercase}
  .headline .l1{display:block;font-size:88px;color:var(--red)}
  .headline .l2{display:block;font-size:92px;color:var(--ink);letter-spacing:-1px}
  .tagline{left:42px;top:336px;font-size:29px;color:var(--ink);letter-spacing:.5px;font-weight:400}
  .tagline b{font-weight:700}
  .dots{left:44px;top:380px;display:flex;gap:3px}
  .dots span{width:6px;height:6px;border-radius:50%;background:var(--red)}
  .dots span:nth-child(5){opacity:.6}.dots span:nth-child(6){opacity:.35}
  .intro{left:42px;top:396px;width:300px;font-size:14.3px;line-height:1.2;color:var(--ink);font-weight:500}

  /* trust card */
  .trust{left:416px;top:420px;width:321px;height:479px;background:var(--red);border-radius:28px 28px 0 28px;padding:28px 27px 0;z-index:2}
  .trust h2{font-style:italic;font-weight:800;font-size:20px;line-height:1.2;text-transform:uppercase;color:#fff}
  .trust h2 span{color:var(--ink)}
  .trust .rule{width:40px;height:3px;background:#fff;margin:12px 0 16px}
  .trust p.lead{font-size:13.3px;line-height:1.16;text-align:justify;color:#fff}
  .feature{display:flex;gap:9px;margin-top:22px}
  .feature .ico{flex:none;width:40px;height:40px;border-radius:50%;background:var(--ink);border:3px solid #fff;display:flex;align-items:center;justify-content:center}
  .feature h3{font-size:18.5px;font-weight:700;line-height:1.1;margin-top:6px}
  .feature p{font-size:13.3px;line-height:1.17;margin-top:3px}

  /* left column */
  .sec-title{font-style:italic;font-weight:800;font-size:15px;text-transform:uppercase;color:#fff;white-space:nowrap}
  .sec-title em{color:var(--red);font-style:italic}
  .industries{left:46px;top:525px}
  .ind-list{list-style:none;margin-top:10px}
  .ind-list li{display:flex;align-items:center;gap:10px;height:38px;font-size:13.5px;font-weight:500;white-space:nowrap}
  .ind-ico{width:25px;height:25px;border-radius:50%;background:var(--green);border:2px solid #cfe9d4;display:flex;align-items:center;justify-content:center}
  .ind-photo{left:247px;top:563px;width:137px;height:164px;border:2px solid #fff;
    background:linear-gradient(180deg,#3d7bd0 0%,#8fb6e4 55%,#9fa3a6 75%,#6c6f71 100%)}
  .tree{left:46px;top:758px}
  .ticks{list-style:none;margin-top:8px}
  .ticks li{display:flex;align-items:center;gap:9px;height:32px;font-size:13.5px;font-weight:500;white-space:nowrap}
  .tick{flex:none;width:13px;height:13px;border-radius:50%;background:var(--green);display:flex;align-items:center;justify-content:center}
  .tree-note{left:253px;top:788px;width:150px;font-size:12.5px;line-height:1.17;color:#fff}
  .services{left:46px;top:898px;width:370px;height:130px}
  .svc-col{position:absolute;list-style:none}
  .svc-col li{display:flex;align-items:flex-start;gap:9px;font-size:13.5px;font-weight:500;line-height:1.15;white-space:nowrap}
  .svc-col .tick{margin-top:3px}
  .svc-a{left:7px;top:36px}.svc-a li{height:50px}
  .svc-b{left:149px;top:36px}.svc-b li{height:33px}
  .svc-c{left:320px;top:36px}.svc-c li{height:50px}

  /* footer */
  .bottom-photo{left:420px;top:852px;width:363px;height:348px;z-index:1}
  .phone-bar{left:0;top:1046px;width:330px;height:48px}
  .phone{left:48px;top:1052px;display:flex;align-items:center;gap:8px;font-size:27px;font-weight:600;color:#fff}
  .contact-bg{left:0;top:1094px;width:460px;height:106px}
  .addr{top:1104px;display:flex;gap:6px;color:var(--ink)}
  .addr h4{font-size:15px;font-weight:600;line-height:1.1}
  .addr p{font-size:13.5px;line-height:1.18}
  .addr-oh{left:58px}.addr-in{left:224px}
  .web{left:58px;top:1167px;display:flex;align-items:center;gap:6px;font-size:13.5px;font-weight:600;color:var(--ink)}
</style>
</head>
<body>
<main class="flyer">

  <section class="hero abs">
    <div class="hero-photo abs" role="img" aria-label="Blue knuckle-boom crane truck lifting a rooftop unit in a gravel lot under a pale sky"></div>
    <div class="brand abs"><span class="brand-dot"></span><span class="brand-name">Hoist Ridge Crane</span></div>
    <h1 class="headline abs"><span class="l1">Crane</span><span class="l2">Service</span></h1>
    <p class="tagline abs">DONE AS <b>PROMISED</b></p>
    <div class="dots abs"><span></span><span></span><span></span><span></span><span></span><span></span></div>
    <p class="intro abs">Crane service partners that meet deadlines, prioritize safety, and stay within budget with end-to-end support.</p>
  </section>

  <section class="industries abs">
    <h2 class="sec-title">Industries <em>We Serve</em></h2>
    <ul class="ind-list">
      <li><span class="ind-ico"><svg width="11" height="11" viewBox="0 0 12 12"><circle cx="6" cy="5" r="4" fill="none" stroke="#fff" stroke-width="1.4"/><path d="M6 8v4" stroke="#fff" stroke-width="1.4"/></svg></span>Tree &amp; Landscape</li>
      <li><span class="ind-ico"><svg width="11" height="11" viewBox="0 0 12 12"><path d="M1 11L11 1M3 6h6" stroke="#fff" stroke-width="1.4"/></svg></span>Steel Construction</li>
      <li><span class="ind-ico"><svg width="11" height="11" viewBox="0 0 12 12"><rect x="1.5" y="2.5" width="9" height="7" fill="none" stroke="#fff" stroke-width="1.4"/></svg></span>HVAC Lifts</li>
      <li><span class="ind-ico"><svg width="11" height="11" viewBox="0 0 12 12"><path d="M6 1v10M3 4h6" stroke="#fff" stroke-width="1.4"/></svg></span>General Construction</li>
      <li><span class="ind-ico"><svg width="11" height="11" viewBox="0 0 12 12"><rect x="1" y="4" width="10" height="6" fill="#fff"/></svg></span>Container Lifts</li>
    </ul>
  </section>
  <div class="ind-photo abs" role="img" aria-label="Crane setting a steel beam beside a building under a blue sky"></div>

  <section class="tree abs">
    <h2 class="sec-title">Tree Removal <em>Crane Rentals</em></h2>
    <ul class="ticks">
      <li><span class="tick"><svg width="7" height="7" viewBox="0 0 8 8"><path d="M1 4l2 2 4-4" fill="none" stroke="#fff" stroke-width="1.6"/></svg></span>Experienced operators</li>
      <li><span class="tick"><svg width="7" height="7" viewBox="0 0 8 8"><path d="M1 4l2 2 4-4" fill="none" stroke="#fff" stroke-width="1.6"/></svg></span>Minimize time delays</li>
      <li><span class="tick"><svg width="7" height="7" viewBox="0 0 8 8"><path d="M1 4l2 2 4-4" fill="none" stroke="#fff" stroke-width="1.6"/></svg></span>Flexible scheduling</li>
    </ul>
  </section>
  <p class="tree-note abs">We ensure your tree service projects are completed safely, efficiently, and without property damage.</p>

  <section class="services abs">
    <h2 class="sec-title">Our <em>Services</em></h2>
    <ul class="svc-col svc-a">
      <li><span class="tick"><svg width="7" height="7" viewBox="0 0 8 8"><path d="M1 4l2 2 4-4" fill="none" stroke="#fff" stroke-width="1.6"/></svg></span>General<br>Construction</li>
      <li><span class="tick"><svg width="7" height="7" viewBox="0 0 8 8"><path d="M1 4l2 2 4-4" fill="none" stroke="#fff" stroke-width="1.6"/></svg></span>Power<br>Transformer</li>
    </ul>
    <ul class="svc-col svc-b">
      <li><span class="tick"><svg width="7" height="7" viewBox="0 0 8 8"><path d="M1 4l2 2 4-4" fill="none" stroke="#fff" stroke-width="1.6"/></svg></span>Steel Construction</li>
      <li><span class="tick"><svg width="7" height="7" viewBox="0 0 8 8"><path d="M1 4l2 2 4-4" fill="none" stroke="#fff" stroke-width="1.6"/></svg></span>Tree Landscape</li>
      <li><span class="tick"><svg width="7" height="7" viewBox="0 0 8 8"><path d="M1 4l2 2 4-4" fill="none" stroke="#fff" stroke-width="1.6"/></svg></span>HVAC</li>
    </ul>
    <ul class="svc-col svc-c">
      <li><span class="tick"><svg width="7" height="7" viewBox="0 0 8 8"><path d="M1 4l2 2 4-4" fill="none" stroke="#fff" stroke-width="1.6"/></svg></span>Container &amp;<br>Cargo Crane</li>
      <li><span class="tick"><svg width="7" height="7" viewBox="0 0 8 8"><path d="M1 4l2 2 4-4" fill="none" stroke="#fff" stroke-width="1.6"/></svg></span>Heavy Machinery<br>Moving</li>
    </ul>
  </section>

  <svg class="bottom-photo abs" viewBox="0 0 363 348" role="img" aria-label="Red knuckle-boom crane truck working beside a brick building with trees">
    <defs>
      <linearGradient id="redCraneTone" x1="0" y1="0" x2="1" y2="1">
        <stop offset="0" stop-color="#2a2a2c"/>
        <stop offset=".45" stop-color="#8a6a4a"/>
        <stop offset=".75" stop-color="#4d5a3a"/>
        <stop offset="1" stop-color="#2b2b2b"/>
      </linearGradient>
    </defs>
    <polygon points="170,0 363,0 363,348 0,348 0,300 120,300 170,200" fill="url(#redCraneTone)" opacity=".9"/>
  </svg>

  <aside class="trust abs">
    <h2>Trusted Crane<br><span>Company in OH. &amp; IN.</span></h2>
    <div class="rule"></div>
    <p class="lead">Our team of project planners and operators is committed to serving your project’s needs every step of the way, ensuring safety and done right the first time without major disruptions.</p>
    <div class="feature">
      <span class="ico"><svg width="18" height="18" viewBox="0 0 20 20"><circle cx="10" cy="10" r="6" fill="none" stroke="#fff" stroke-width="1.6"/><circle cx="10" cy="10" r="2" fill="#fff"/><path d="M10 1v3M10 16v3M1 10h3M16 10h3" stroke="#fff" stroke-width="1.6"/></svg></span>
      <div><h3>Fastest Workflow</h3><p>Our well-maintained cranes &amp;<br>skilled operators deliver a<br>smooth experience.</p></div>
    </div>
    <div class="feature">
      <span class="ico"><svg width="16" height="16" viewBox="0 0 20 20"><rect x="4" y="2" width="12" height="16" rx="1" fill="none" stroke="#fff" stroke-width="1.6"/><path d="M7 7h6M7 11h6M7 15h3" stroke="#fff" stroke-width="1.6"/></svg></span>
      <div><h3>Budget Friendly</h3><p>We send the right size crane<br>to get the job done safely, so<br>you don’t overpay for what you<br>don’t use.</p></div>
    </div>
  </aside>

  <svg class="phone-bar abs" viewBox="0 0 330 48" aria-hidden="true"><polygon points="0,0 296,0 330,48 0,48" fill="var(--red)"/></svg>
  <div class="phone abs">
    <svg width="22" height="22" viewBox="0 0 24 24"><path d="M6.6 10.8a15 15 0 006.6 6.6l2.2-2.2a1 1 0 011-.25 11.4 11.4 0 003.6.57 1 1 0 011 1V20a1 1 0 01-1 1A17 17 0 013 4a1 1 0 011-1h3.5a1 1 0 011 1c0 1.25.2 2.45.57 3.57a1 1 0 01-.25 1z" fill="#fff"/></svg>
    (555) 417-2093
  </div>

  <svg class="contact-bg abs" viewBox="0 0 460 106" aria-hidden="true"><polygon points="0,0 420,0 460,40 460,106 0,106" fill="#fff"/><polygon points="380,0 460,0 460,60" fill="var(--dark)"/></svg>
  <div class="addr addr-oh abs">
    <svg width="12" height="16" viewBox="0 0 12 16"><path d="M6 0a6 6 0 016 6c0 4.5-6 10-6 10S0 10.5 0 6a6 6 0 016-6z" fill="var(--red)"/><circle cx="6" cy="6" r="2.2" fill="#fff"/></svg>
    <div><h4>Ohio</h4><p>480 Maple Row, Akron,<br>OH 44300</p></div>
  </div>
  <div class="addr addr-in abs">
    <svg width="12" height="16" viewBox="0 0 12 16"><path d="M6 0a6 6 0 016 6c0 4.5-6 10-6 10S0 10.5 0 6a6 6 0 016-6z" fill="var(--red)"/><circle cx="6" cy="6" r="2.2" fill="#fff"/></svg>
    <div><h4>Indiana</h4><p>7710 Creek Ln,<br>Noblesville, IN 46000</p></div>
  </div>
  <div class="web abs">
    <svg width="13" height="13" viewBox="0 0 14 14"><circle cx="7" cy="7" r="6" fill="none" stroke="var(--red)" stroke-width="1.5"/><path d="M1 7h12M7 1c-3 3-3 9 0 12M7 1c3 3 3 9 0 12" fill="none" stroke="var(--red)" stroke-width="1.2"/></svg>
    HoistRidgeCranes.example
  </div>

</main>
</body>
</html>
```